Sophisticated, clean website reflecting my feminine, playful side to sell my abstract art,

I need a website no more than 3 pages to showcase my paintings, a little about me and some contact info. I do abstracts so looking for something a little edgy, yet feminine and current.
Updates

Hi there, These are some artists websites that I Iike: Marnelvoss.com (I like how airy it is) peterwallombry.com garethpolvens.com (I like how it scrolls) I'll need a place for a photo ( a headshot-i do not have it yet so I'll need to be able to upload that later) as well as an area for my bio. Also, it's important that I will be able to upload any new photos and descriptions easily so it should be user friendly. Lastly, I like in a sunny place so would like to have this seem upbeat and playful as that is how i like to paint. thanks-I'm trying to upload my photos now -

Target Market(s)

ppl ages 35-70 who want large scale art for their homes

Industry/Entity Type

art

Coding

Coded - Design and coding required

Number of Pages Required

3 page

Colors

Designer to choose colors to be used in the design.

Requirements
Must have
• photos of my art, a place for my bio, be easy to reach me. tasteful-nothing too "in your face" -my clients are pretty high end and organized. They like clean lines
Nice to have
• sophisticated background, muted tones in the back-similar clean font throughout-no cursive
Should not have
• too many dark areas. Too many blocks of color. Too serious.

```html
<!DOCTYPE html>
<html lang="en">
<head>
<meta charset="utf-8">
<title>Modren Classic Arts</title>
<link href="https://fonts.googleapis.com/css2?family=Gilda+Display&family=EB+Garamond:wght@400;500&family=Poppins:wght@400;500;600&display=swap" rel="stylesheet">
<style>
:root{
  --ink:#1d1b1a;
  --accent:#c27461;
  --blush:#fdf3f2;
  --sand:#ddd3c2;
  --footer:#c4a988;
  --white:#ffffff;
  --muted:#8f8a86;
  --display:"Gilda Display", Georgia, serif;
  --serif:"EB Garamond", Georgia, serif;
  --sans:"Poppins", Arial, sans-serif;
}
*{box-sizing:border-box;margin:0;padding:0}
html,body{width:1200px;height:4090px;overflow:hidden}
body{position:relative;background:var(--white);color:var(--ink);font-family:var(--serif)}
.abs{position:absolute}
.btn{position:absolute;display:flex;align-items:center;justify-content:center;background:var(--accent);color:var(--white);font-family:var(--serif);font-size:16px;letter-spacing:.5px}
.art{position:absolute}
p{font-size:16.5px;line-height:19px}

/* hero */
.hero{left:0;top:0;width:1200px;height:581px;background:var(--blush)}
.logo{left:64px;top:28px;font-family:var(--display);font-size:32px}
.nav{top:38px;font-size:18.5px}
.hero-title{left:64px;top:170px;font-family:var(--display);font-size:56px;line-height:56px;letter-spacing:1px}
.hero-sub{left:64px;top:296px;font-family:var(--display);font-size:29px;line-height:30px;letter-spacing:.5px}
.hero-art{left:449px;top:113px;width:707px;height:419px;background:linear-gradient(135deg,#e7e0da 0%,#7d5aa0 35%,#c9b2cf 55%,#5e3e82 75%,#e2dbd6 100%);box-shadow:0 10px 30px rgba(0,0,0,.12)}
.arrow{position:absolute;top:305px;width:35px;height:35px;background:var(--accent);display:flex;align-items:center;justify-content:center}

/* sections */
.section-title{width:1200px;text-align:center;font-family:var(--display);font-size:40px;letter-spacing:1px}
.eyebrow{font-family:var(--serif);color:var(--accent);font-size:21px;letter-spacing:.5px}
.heading{font-family:var(--display);font-size:34px;letter-spacing:.5px}

/* showcase */
.showcase{left:0;top:1232px;width:1200px;height:549px;background:var(--sand)}
.card{position:absolute;top:1368px;width:199px;height:275px;background:var(--white)}
.card .thumb{position:absolute;left:16px;top:13px;width:167px;height:171px}
.card .name{position:absolute;top:193px;width:100%;text-align:center;font-size:15px}
.card .price{position:absolute;top:216px;width:100%;text-align:center;font-size:9.5px;font-family:var(--sans);font-weight:600}
.card .price s{color:var(--muted);font-weight:400;margin-right:6px}
.card .cart{position:absolute;left:57px;top:237px;width:85px;height:18px;background:var(--accent);color:var(--white);font-size:9px;display:flex;align-items:center;justify-content:center;letter-spacing:.4px}

/* contact */
.contact-band{left:0;top:2416px;width:1200px;height:624px;background:linear-gradient(180deg,#fbeeee,#fdf7f6)}
.contact-card{left:92px;top:2521px;width:1016px;height:447px;background:var(--white);box-shadow:0 8px 28px rgba(0,0,0,.08)}
.form{left:222px;top:2564px;width:330px;height:360px;background:var(--sand)}
.form-lead{left:26px;top:36px;width:290px;color:var(--white);font-size:19px;line-height:20px;letter-spacing:.4px}
.field{position:absolute;left:27px;width:276px;height:23px;background:var(--white);font-size:9px;color:var(--muted);padding:5px 14px}

/* feedback */
.quote-mark{left:880px;top:3010px;font-family:var(--display);font-size:420px;line-height:420px;color:var(--sand)}
.review{position:absolute;top:3206px;width:450px;height:183px;background:var(--white);box-shadow:0 6px 20px rgba(0,0,0,.09);text-align:center}
.review h4{margin-top:38px;font-family:var(--sans);font-weight:500;font-size:15px}
.review p{margin:14px 44px 0;font-size:11px;line-height:20px;color:#aaa4a0}
.person{position:absolute;top:3414px;display:flex;align-items:center;gap:14px}
.avatar{width:44px;height:44px;border-radius:50%;background:linear-gradient(135deg,#e8cfc9,#b78b83)}
.person b{display:block;font-family:var(--sans);font-weight:600;font-size:15px;color:#555}
.person small{font-family:var(--sans);font-size:11px;color:#555}

/* gallery strip */
.tile{position:absolute;top:3511px;height:227px}

/* footer */
.footer{left:0;top:3738px;width:1200px;height:352px;background:var(--footer);color:var(--white)}
.fcol{position:absolute;top:62px}
.fcol h5{font-family:var(--display);font-weight:400;font-size:23px;letter-spacing:1px;margin-bottom:14px}
.fcol ul{list-style:none;font-family:var(--sans);font-size:12.5px}
.fcol li{position:relative;padding-left:34px;height:26px}
.fcol li::before{content:"";position:absolute;left:0;top:7px;width:6px;height:6px;border-radius:50%;background:var(--white)}
.fcol .about{font-family:var(--sans);font-size:11.5px;line-height:17px;width:220px}
.contact-row{display:flex;align-items:center;gap:18px;font-family:var(--sans);font-size:17px;height:44px}
.rule{left:64px;top:4027px;width:1072px;height:1px;background:rgba(255,255,255,.35)}
.copyright{left:0;top:4040px;width:1200px;text-align:center;font-family:var(--sans);font-size:13px}
</style>
</head>
<body>

<!-- hero -->
<div class="abs hero"></div>
<div class="abs logo">Logo Here</div>
<div class="abs nav" style="left:529px">Home</div>
<div class="abs nav" style="left:621px">About me</div>
<div class="abs nav" style="left:745px">showcase my paintings</div>
<div class="btn" style="left:1032px;top:30px;width:111px;height:37px;font-size:17px">Contact us</div>
<h1 class="abs hero-title" style="font-weight:400">Modren<br>Classic Arts</h1>
<div class="abs hero-sub">Artworks that speak<br>a million words</div>
<div class="btn" style="left:63px;top:384px;width:131px;height:35px;background:#000">Explore More</div>
<div class="art hero-art" role="img" aria-label="Featured abstract painting in purple, violet and cream brushstrokes"></div>
<div class="arrow" style="left:449px"><svg width="18" height="12" viewBox="0 0 18 12"><path d="M17 6H2M6 1L1 6l5 5" stroke="#1d1b1a" stroke-width="1.6" fill="none"/></svg></div>
<div class="arrow" style="left:1121px"><svg width="18" height="12" viewBox="0 0 18 12"><path d="M1 6h15M12 1l5 5-5 5" stroke="#1d1b1a" stroke-width="1.6" fill="none"/></svg></div>

<!-- exhibitions -->
<h2 class="abs section-title" style="top:645px;font-weight:400">Exhibitions</h2>
<div class="art" style="left:140px;top:789px;width:409px;height:346px;background:linear-gradient(135deg,#d9a69a,#a9645a 40%,#e8c7bf 65%,#3d2630 100%)" role="img" aria-label="Abstract painting of pink and rust floral swirls"></div>
<div class="abs eyebrow" style="left:654px;top:806px">About</div>
<div class="abs heading" style="left:651px;top:836px">Exhibitions</div>
<div class="abs" style="left:651px;top:886px;width:486px">
  <p>Lorem ipsum dolor sit amet, consectetur estor adipi isicing elit, sed do eiusmod tempor este uterre incididui unt ut labore et dolore magna aliquaas. Ut enim ad minim veniam, quis mot nostrud desto exercitation est ullamco laboris nisi ut se aliquip ex ea commodos consequat.</p>
  <p style="margin-top:19px">Duis aute irure et dolor in reprehender itinse voluptate velit esse cillum dolore eu fugiat do nulla pariatur deus ex. Excepteur sint occaecat er cupidatat non ullamco proident, sunt in dos<br>Lorem ipsum dolor sit amet, consectetur adipisic eli sed do eiusmod tempor incididunt ut labore et dolore si magna</p>
</div>
<div class="btn" style="left:651px;top:1090px;width:128px;height:35px">Contact us</div>

<!-- showcase -->
<div class="abs showcase"></div>
<h2 class="abs section-title" style="top:1282px;font-weight:400;font-size:34px">Showcase My Paintings</h2>
<div class="card" style="left:151px"><div class="thumb" role="img" aria-label="Abstract painting in ochre, navy and rust" style="background:linear-gradient(135deg,#d49a2c,#2b3b6b 55%,#c9673f)"></div><div class="name">Lorem ipsum</div><div class="price"><s>$ 45.000</s>$ 35.000</div><div class="cart">ADD TO CART</div></div>
<div class="card" style="left:384px"><div class="thumb" role="img" aria-label="Abstract painting in violet and cream" style="background:linear-gradient(135deg,#e6e0dc,#6d4f94 50%,#d8d0d8)"></div><div class="name">Lorem ipsum</div><div class="price"><s>$ 45.000</s>$ 35.000</div><div class="cart">ADD TO CART</div></div>
<div class="card" style="left:617px"><div class="thumb" role="img" aria-label="Abstract painting in deep rust and cream" style="background:linear-gradient(135deg,#efe3dc,#a2402b 50%,#e0c8bb)"></div><div class="name">Lorem ipsum</div><div class="price"><s>$ 45.000</s>$ 35.000</div><div class="cart">ADD TO CART</div></div>
<div class="card" style="left:851px"><div class="thumb" role="img" aria-label="Abstract painting in teal, black and cream" style="background:linear-gradient(135deg,#e7e2dc,#1f7f86 45%,#2a2a2a 70%,#d8d3cc)"></div><div class="name">Lorem ipsum</div><div class="price"><s>$ 45.000</s>$ 35.000</div><div class="cart">ADD TO CART</div></div>
<div class="btn" style="left:537px;top:1692px;width:128px;height:35px">Explore More</div>

<!-- works of art -->
<div class="abs eyebrow" style="left:70px;top:1949px">The Museum archive</div>
<div class="abs heading" style="left:70px;top:1980px">WORKS OF ART</div>
<div class="abs" style="left:70px;top:2035px;width:490px">
  <p>Lorem ipsum dolor sit amet, consectetur estor adipi isicing elit, sed do eiusmod tempor este uterre incididui unt ut labore et dolore magna aliquaas. Ut enim ad minim veniam, quis mot nostrud desto exercitation est ullamco laboris nisi ut se aliquip ex ea commodos consequat.</p>
  <p style="margin-top:19px">Duis aute irure et dolor in reprehender itinse voluptate velit esse cillum dolore eu fugiat do nulla pariatur deus ex. Excepteur sint occaecat er cupidatat non ullamco proident, sunt in dos<br>Lorem ipsum dolor sit amet, consectetur adipisic eli sed do eiusmod tempor incididunt ut labore et dolore si magna aliqua. Ut enim adese</p>
</div>
<div class="btn" style="left:70px;top:2260px;width:128px;height:35px">Contact us</div>
<div class="art" style="left:1032px;top:2240px;width:130px;height:90px;background:#fbeceb" role="img" aria-label="Decorative dot grid accent"></div>
<div class="art" style="left:698px;top:1940px;width:434px;height:368px;background:linear-gradient(135deg,#d9a69a,#a9645a 40%,#e8c7bf 65%,#3d2630 100%)" role="img" aria-label="Abstract painting of pink and rust floral swirls"></div>

<!-- contact -->
<div class="abs contact-band"></div>
<div class="abs contact-card"></div>
<div class="abs form">
  <div class="abs form-lead">Fill the form if you want to get more information about painting</div>
  <div class="field" style="top:99px">Enter Your Name</div>
  <div class="field" style="top:133px">Enter Your Email</div>
  <div class="field" style="top:167px">Enter Your Number</div>
  <div class="field" style="top:202px;height:92px">write massage</div>
  <div class="btn" style="left:27px;top:308px;width:70px;height:30px;font-size:17px">Send</div>
</div>
<div class="abs eyebrow" style="left:635px;top:2576px">Events</div>
<div class="abs heading" style="left:635px;top:2609px">Get in Touch</div>
<div class="abs" style="left:635px;top:2665px;width:405px">
  <p>Lorem ipsum dolor sit amet, consectetur estor adipi isicing elit, sed do eiusmod tempor este uterre incididui unt ut labore et dolore magna aliquaas. Ut enim ad minim veniam, quis mot nostrud desto exercitation est ullamco laboris nisi ut se aliquip ex ea commodos consequat.</p>
  <p style="margin-top:19px">Duis aute irure et dolor in reprehender itinse voluptate velit esse cillum dolore eu fugiat do nulla pariatur deus ex. Excepteur sint occaecat er cupidatat non ullamco proident, sunt in dos Lorem ipsum dolor sit amet, consectetur adipisic eli sed do eiusmod tempor incididunt ut labore et dolore si magna aliqua. Ut enim adese</p>
</div>

<!-- feedback -->
<div class="abs quote-mark">&ldquo;</div>
<h2 class="abs section-title" style="top:3118px;font-weight:400;font-size:34px">Client Feedback</h2>
<div class="review" style="left:130px"><h4>Lorem ipsum dolor</h4><p>Lorem ipsum dolor sit amet, consectetur adipiscing elit. Etiam velit auctor pellentesque risus, donec donec pulvinar. Morbi orci pulvinar leo pellentesque et at pellentesque. Id vitae arcu nulla non. Pellentesque blandit lorem interdum egestas non hendrerit nisl, blandit tellus.</p></div>
<div class="review" style="left:619px"><h4>Lorem ipsum dolor</h4><p>Lorem ipsum dolor sit amet, consectetur adipiscing elit. Etiam velit auctor pellentesque risus, donec donec pulvinar. Morbi orci pulvinar leo pellentesque et at pellentesque. Id vitae arcu nulla non. Pellentesque blandit lorem interdum egestas non hendrerit nisl, blandit tellus.</p></div>
<div class="person" style="left:263px"><div class="avatar" role="img" aria-label="Client portrait photo"></div><div><b>Ivo Ramsay</b><small>Vores turist</small></div></div>
<div class="person" style="left:753px"><div class="avatar" role="img" aria-label="Client portrait photo"></div><div><b>Jana Cooke</b><small>Vores turist</small></div></div>

<!-- gallery strip -->
<div class="tile" style="left:0;width:302px;background:linear-gradient(180deg,#d9d4cc,#1d3b6a 45%,#1b8f92 85%)" role="img" aria-label="Abstract painting detail in navy and teal"></div>
<div class="tile" style="left:302px;width:298px;background:linear-gradient(135deg,#c98575,#b06a5e 50%,#d49a8a)" role="img" aria-label="Abstract painting detail in terracotta pink"></div>
<div class="tile" style="left:600px;width:306px;background:linear-gradient(135deg,#d9d1c7,#1e6f78 45%,#2b2b2b 65%,#cfc5b8)" role="img" aria-label="Abstract painting detail in teal and black burst"></div>
<div class="tile" style="left:906px;width:294px;background:linear-gradient(90deg,#e3d9cf,#bfa98f 55%,#1f6fa0)" role="img" aria-label="Abstract painting detail in sand and blue"></div>

<!-- footer -->
<footer class="abs footer">
  <div class="fcol" style="left:116px"><h5>LOGO HERE</h5><div class="about">lorem ipsum dolor sit amet, consectetur adipiscing elit, viverra et pellentesque leo imperdiet quis. a diam ut natoque amet sodales, id amet, viverra vitae et enim.</div></div>
  <div class="fcol" style="left:411px"><h5>QUCIK LINKS</h5><ul><li>Home</li><li>About me</li><li>showcase my paintings</li><li>Contact us</li></ul></div>
  <div class="fcol" style="left:660px"><h5>CUSTOMER CARE</h5><ul><li>gift card balance</li><li>Acount</li><li>Shipping Policy</li><li>Care &amp; Repair</li><li>FAQ</li></ul></div>
  <div class="fcol" style="left:937px"><h5>CONTACT US</h5>
    <div class="contact-row"><svg width="20" height="20" viewBox="0 0 24 24"><path d="M6.6 10.8a15 15 0 006.6 6.6l2.2-2.2c.3-.3.7-.4 1-.2 1.1.4 2.3.6 3.6.6.6 0 1 .4 1 1V20c0 .6-.4 1-1 1A17 17 0 013 4c0-.6.4-1 1-1h3.5c.6 0 1 .4 1 1 0 1.3.2 2.5.6 3.6.1.3 0 .7-.2 1z" fill="#fff"/></svg>080-000-000</div>
    <div class="contact-row"><svg width="22" height="16" viewBox="0 0 22 16"><rect x="1" y="1" width="20" height="14" fill="none" stroke="#fff" stroke-width="1.4"/><path d="M1 1l10 8 10-8" fill="none" stroke="#fff" stroke-width="1.4"/></svg>Email Us</div>
    <div class="contact-row"><svg width="20" height="22" viewBox="0 0 20 24"><path d="M10 23s8-8 8-14a8 8 0 00-16 0c0 6 8 14 8 14z" fill="none" stroke="#fff" stroke-width="1.4"/><circle cx="10" cy="9" r="3" fill="none" stroke="#fff" stroke-width="1.4"/></svg>Get Direction</div>
  </div>
</footer>
<div class="abs rule"></div>
<div class="abs copyright" style="color:#fff">Copyright 2021 All Rights Reserved</div>

</body>
</html>
```